Redo a PPT pres. - Real Estate in Brazil - Socially equitable investments in Social Housing

We need to redo the presentation attached. It is an institutional presentation to attract local and foreign investors to invest in Brazilian Social Housing Projects structured by our company "TLR".
A middle class of 100 million, a housing deficit of 9M, a strong political will & positive income generation trends constitute grounds for a significant demand in social housing.
This make a perfect scheme for investors to invest in Brazilian Social Housing.
"TLR", is a consulting "boutique" focused in Brazilian real estate, specialized in structuring, analyzing and originating Brazilian social housing projects.
TLR is part of the group TLB. TLB is structured to create value through each step of the residential real estate business - structuring, financing, sales, marketing and technology.
We would like to see designs that use mainly the color blue. The final design should communicate financial safety and professionalism. In order to reach our needs, the designer will need to have basic understanding of finance and investment in order to highlight the most important information.
The idea is to receive back the PPT with each page redesigned and an homogeneous identity.
To all designers,
Target Market(s)
Institutional Investors and wealthy individuals
Industry/Entity Type
Residential
Look and feel

```html
<!DOCTYPE html>
<html lang="en">
<head>
<meta charset="UTF-8">
<title>TLR – Investor Presentation Slides</title>
<link href="https://fonts.googleapis.com/css2?family=Open+Sans:wght@400;600;700;800&display=swap" rel="stylesheet">
<style>
  :root{
    --stage:#0a0a0a;
    --paper:#ffffff;
    --navy:#1c2b55;
    --blue:#4b5a99;
    --blue-mid:#3b5c98;
    --blue-light:#8fa6cf;
    --ring:#c9d3e6;
    --green:#8cc63f;
    --green-text:#9bd14d;
    --ink:#333842;
    --grid:#e2e5ec;
  }
  *{margin:0;padding:0;box-sizing:border-box}
  html,body{width:1200px;height:520px;overflow:hidden;background:var(--stage)}
  body{position:relative;font-family:"Open Sans",Arial,sans-serif;color:var(--ink)}
  .slide{position:absolute;top:61px;width:534px;height:399px;background:var(--paper);overflow:hidden}
  .slide--politics{left:44px}
  .slide--demographics{left:622px}

  .side-panel{position:absolute;left:0;top:0;width:192px;height:399px}
  .side-panel__photo{position:absolute;inset:0;background:linear-gradient(180deg,#5a7cb8 0%,#3d5f9d 35%,#2c4a86 65%,#1d3566 100%)}
  .side-panel__band{position:absolute;left:0;right:0;top:257px;bottom:0;background:rgba(18,30,62,.72)}
  .ribbon{position:absolute;left:24px;top:0;width:100px;height:50px}
  .ribbon__name{position:absolute;left:0;right:0;top:12px;text-align:center;color:#fff;font-weight:400;font-size:19px;letter-spacing:1px}
  .badge{position:absolute;left:39px;top:122px;width:114px;height:114px;border-radius:50%;background:rgba(255,255,255,.35);display:flex;align-items:center;justify-content:center}
  .badge__inner{width:86px;height:86px;border-radius:50%;background:#fff;border:4px solid var(--ring);display:flex;align-items:center;justify-content:center;color:var(--blue-mid);font-size:11.5px;font-weight:400}
  .headline{position:absolute;left:4px;right:4px;top:268px;color:#fff;font-weight:800;font-size:16.8px;line-height:20px;text-align:center;letter-spacing:.2px}
  .headline__sub{display:block;font-size:11px;margin-top:8px;letter-spacing:.5px}
  .tagline{position:absolute;left:8px;right:8px;color:var(--green-text);font-size:8.4px;line-height:11px;text-align:center}

  .section-tag{position:absolute;height:16px;background:var(--blue);color:#fff;font-weight:700;font-size:8.4px;letter-spacing:.3px;line-height:16px;padding-left:12px;border-radius:2px;box-shadow:1px 2px 3px rgba(0,0,0,.25)}
  .section-tag--title{font-weight:600;font-size:9.5px;padding-left:16px}

  .copy{position:absolute;left:222px;right:13px;font-size:6.6px;line-height:8.4px;color:var(--ink)}
  .copy p{margin-bottom:4px}
  .copy h4{font-size:6.8px;font-weight:700;margin:6px 0 2px}
  .copy ul{list-style:none}
  .copy li{position:relative;padding-left:8px;margin-bottom:0.5px}
  .copy li::before{content:"";position:absolute;left:1px;top:2.8px;width:3px;height:3px;border-radius:50%;background:var(--blue)}
  .copy--spaced li{margin-bottom:4.5px}
  .copy--buyers li{margin-bottom:7px}
  .copy .note{color:var(--blue-light)}

  .arrow-down{position:absolute;left:346px;top:208px}
  .page-no{position:absolute;right:24px;bottom:14px;font-size:9px;font-weight:600;color:var(--blue-mid);letter-spacing:.5px}
  .page-no span{color:var(--blue-light);margin:0 3px}
  .chart{position:absolute;left:200px;top:80px}
</style>
</head>
<body>

<section class="slide slide--politics">
  <div class="side-panel">
    <div class="side-panel__photo" role="img" aria-label="Blue-toned photograph of a city skyline with high-rise buildings"></div>
    <div class="side-panel__band"></div>
    <svg class="ribbon" viewBox="0 0 100 50" aria-hidden="true"><polygon points="0,0 100,0 100,50 50,40 0,50" fill="#1c2b55"/></svg>
    <div class="ribbon"><div class="ribbon__name">TLR</div></div>
    <div class="badge"><div class="badge__inner">Green Light</div></div>
    <h2 class="headline">A MIDDLE CLASS OF<br>100 MILLION PEOPLE</h2>
    <p class="tagline" style="top:340px">Strong political will &amp; positive income generation trends constitute grounds for a significant demand in social housing</p>
  </div>

  <div class="section-tag" style="left:222px;top:40px;width:82px">POLITICS</div>
  <div class="copy" style="top:61px">
    <p>Brazil launched a fierce battle against poverty <b>10 years ago</b> with President Moreira.<br>The positive economic environment has helped implement these policies.</p>
    <h4>Growth Acceleration Program (2007-10): R$400B (*)</h4>
    <ul>
      <li>Public investments in infrastructure</li>
      <li>Lighten the administrative and legal burden on private initiatives and long-term growth</li>
      <li>Stimulating Credit &amp; Financing for the real estate sector</li>
    </ul>
    <h4>Growth Acceleration Program (2011-14): R$960B (*)</h4>
    <ul>
      <li>« Better City » &amp; Community: R$80B</li>
      <li>Water, Light, Transportation: R$135B</li>
      <li>Energy: R$466B</li>
      <li>Housing: R$278B - public financing and subsidizes through various programs, notably Casa Para Todos (CPT) for low and middle classes and Credito Parceria.</li>
    </ul>
  </div>

  <svg class="arrow-down" width="40" height="24" viewBox="0 0 40 24" aria-hidden="true"><polygon points="0,0 40,0 20,24" fill="#8cc63f"/></svg>

  <div class="section-tag" style="left:222px;top:256px;width:197px">EMERGENCE OF THE MIDDLE CLASS</div>
  <div class="copy copy--spaced" style="top:281px">
    <ul>
      <li>It reached remarkable success: poverty has <b>decreased from 39% of population in 1999</b> to <b>less than 20% in 2012</b>.</li>
      <li><b>More than 40M people</b> have recently entered the middle class. They need decent housing.</li>
      <li><b>Middle class will represent 54% of the population by the end of 2012</b> (overall population of 197M).</li>
      <li>Constitution of an upper middle class with <b>an appetite</b> for pricier products.</li>
      <li>Housing deficit is estimated to be around <b>9M</b>, of which <b>7M in urban housing</b>.</li>
    </ul>
  </div>
  <div class="page-no"><span>‹</span>04<span>›</span></div>
</section>

<section class="slide slide--demographics">
  <div class="side-panel">
    <div class="side-panel__photo" role="img" aria-label="Blue-toned photograph of a city skyline with high-rise buildings"></div>
    <div class="side-panel__band"></div>
    <svg class="ribbon" viewBox="0 0 100 50" aria-hidden="true"><polygon points="0,0 100,0 100,50 50,40 0,50" fill="#1c2b55"/></svg>
    <div class="ribbon"><div class="ribbon__name">TLR</div></div>
    <div class="badge"><div class="badge__inner">Green Light</div></div>
    <h2 class="headline">A MIDDLE CLASS OF<br>100 MILLION PEOPLE<span class="headline__sub">AND STILL GROWING</span></h2>
    <p class="tagline" style="top:350px">Positive demographics &amp; economic environment will sustain the demand</p>
  </div>

  <div class="section-tag section-tag--title" style="left:215px;top:37px;width:166px">Number of people based on ages</div>

  <svg class="chart" width="320" height="150" viewBox="0 0 320 150" aria-label="Population by age group, 2000 versus 2020">
    <g stroke="#e2e5ec" stroke-width="1">
      <line x1="78" y1="4" x2="78" y2="92"/><line x1="124.8" y1="4" x2="124.8" y2="92"/>
      <line x1="171.6" y1="4" x2="171.6" y2="92"/><line x1="218.4" y1="4" x2="218.4" y2="92"/>
      <line x1="265.2" y1="4" x2="265.2" y2="92"/>
    </g>
    <g fill="#8cc63f">
      <rect x="78" y="6" width="60.8" height="7"/><rect x="78" y="16" width="79.6" height="7"/>
      <rect x="78" y="26" width="121.7" height="7"/><rect x="78" y="36" width="149.8" height="7"/>
      <rect x="78" y="46" width="163.8" height="7"/><rect x="78" y="56" width="159.1" height="7"/>
      <rect x="78" y="66" width="168.5" height="7"/><rect x="78" y="76" width="166.1" height="7"/>
    </g>
    <g fill="#4b5a99">
      <rect x="78" y="6" width="28.1" height="7"/><rect x="78" y="16" width="42.1" height="7"/>
      <rect x="78" y="26" width="60.8" height="7"/><rect x="78" y="36" width="93.6" height="7"/>
      <rect x="78" y="46" width="131" height="7"/><rect x="78" y="56" width="154.4" height="7"/>
      <rect x="78" y="66" width="163.8" height="7"/><rect x="78" y="76" width="163.8" height="7"/>
    </g>
    <g font-family="Open Sans, Arial, sans-serif" font-size="6.6" fill="#333842" text-anchor="end">
      <text x="72" y="22">60-70 years</text><text x="72" y="42">40-50 years</text>
      <text x="72" y="62">20-30 years</text><text x="72" y="82">0-10 years</text>
    </g>
    <g font-family="Open Sans, Arial, sans-serif" font-size="6.6" fill="#333842" text-anchor="middle">
      <text x="80" y="107">0M</text><text x="126" y="107">10M</text><text x="173" y="107">20M</text>
      <text x="220" y="107">30M</text><text x="268" y="107">40M</text>
    </g>
    <g font-family="Open Sans, Arial, sans-serif" font-size="6.6" fill="#333842">
      <rect x="87" y="133" width="11" height="8" fill="#4b5a99"/><text x="104" y="140">2000 (176 M)</text>
      <rect x="183" y="133" width="11" height="8" fill="#8cc63f"/><text x="201" y="140">2020 (208 M)</text>
    </g>
  </svg>

  <div class="section-tag" style="left:215px;top:264px;width:98px">END BUYERS</div>
  <div class="copy copy--buyers" style="left:240px;top:289px">
    <ul>
      <li>Aging population: Average number of persons per household shrunk from <b>3.7 in 1991 to 3.1 in 2010</b> (1). Expected to remain around 3.</li>
      <li>Projection of <b>12M more people by 2020</b>.<br><span class="note">Natural increase in number of households / housing demand.</span></li>
      <li>Low and stable unemployment rate, <b>6%</b>.</li>
      <li>Considerable growth in real wages, <b>average 5.5% from 2005-2012</b>.<br><span class="note">29M more people will have entered Class C from 2008 to 2014.</span></li>
    </ul>
  </div>
  <div class="page-no"><span>‹</span>05<span>›</span></div>
</section>

</body>
</html>
```